GTP biz card

We need a business card design for our new company based in Los Angeles called "Gold Tide Pictures". We develop film and television projects. We work with investors, financiers, film production companies, film distribution and sales companies as well as studios. We would like to incorporate our logo (see attached) on a two-sided card. We need to include: name and title, address, phone, email and company website.

Target Market(s)

Business, financial and studio clients

Industry/Entity Type

Business

Contact Information for Business Card

Two-sided. We are thinking of the logo on one side and the information on the back. Please feel free to be creative! Thanks.

Requirements
Must have
• Please include the following text information, excluding the "CAPS CATEGORY:" and please allow the ability for us to change the name, title and email address for each company employee):
• NAME & TITLE:
• Neil Parker
• Managing Partner
• COMPANY NAME:
• GOLD TIDE PICTURES (please use existing logo)
• COMPANY ADDRESS:
• KTW Studio Park
• 2250 Halverd Street
• Harbor Wing, 4th Floor
• Manhattan Beach, CA 90412
• COMPANY PHONE NUMBER:
• 310-555-0148
• COMPANY WEBSITE ADDRESS:
• www.goldtidepicturesgroup.example
• EMAIL ADDRESS: (only one per card)
• peter@goldtidepicturesgroup.example
• bingo@goldtidepicturesgroup.example
• neil@goldtidepicturesgroup.example

```html
<!DOCTYPE html>
<html lang="en">
<head>
<meta charset="utf-8">
<title>Gold Tide Pictures – Business Card</title>
<link href="https://fonts.googleapis.com/css2?family=Alegreya+Sans+SC:wght@300;400;500&display=swap" rel="stylesheet">
<style>
  :root {
    --backdrop: #ebebeb;
    --card-black: #050708;
    --card-white: #ffffff;
    --accent: #1fb3e8;
    --accent-deep: #0e7fb8;
    --ink: #1a1a1a;
    --shadow: rgba(0, 0, 0, 0.28);
  }
  * { box-sizing: border-box; margin: 0; padding: 0; }
  html, body {
    width: 963px;
    height: 1200px;
    overflow: hidden;
  }
  body {
    position: relative;
    background: var(--backdrop);
    font-family: "Alegreya Sans SC", sans-serif;
    color: var(--ink);
  }
  .card {
    position: absolute;
    left: 149px;
    width: 656px;
    height: 383px;
    box-shadow: 3px 4px 8px var(--shadow);
    overflow: hidden;
  }
  .card--front {
    top: 171px;
    background: var(--card-black);
  }
  .card--back {
    top: 645px;
    background: var(--card-white);
  }

  /* Brand lockup: plain circle + company name */
  .brand {
    position: absolute;
    display: flex;
    flex-direction: column;
    align-items: center;
  }
  .brand__dot {
    border-radius: 50%;
    background: var(--accent-deep);
  }
  .brand__name {
    font-family: "Alegreya Sans SC", sans-serif;
    font-weight: 500;
    color: var(--accent);
    letter-spacing: 0.06em;
    white-space: nowrap;
  }
  .card--front .brand {
    left: 0;
    right: 0;
    top: 108px;
  }
  .card--front .brand__dot { width: 110px; height: 110px; margin-bottom: 34px; }
  .card--front .brand__name { font-size: 30px; }

  .back__panel {
    position: absolute;
    left: 0;
    top: 0;
    width: 263px;
    height: 100%;
    background: var(--card-black);
    border-right: 4px solid var(--accent);
  }
  .back__panel .brand {
    left: 0;
    right: 0;
    top: 112px;
  }
  .back__panel .brand__dot { width: 74px; height: 74px; margin-bottom: 26px; }
  .back__panel .brand__name { font-size: 19px; }

  .details {
    position: absolute;
    left: 267px;
    right: 0;
    top: 0;
    bottom: 0;
  }
  .person {
    text-align: center;
    margin-top: 34px;
  }
  .person__name {
    font-weight: 400;
    font-size: 30px;
    letter-spacing: 0.12em;
    line-height: 1;
  }
  .person__title {
    font-weight: 400;
    font-size: 17px;
    letter-spacing: 0.16em;
    text-transform: uppercase;
    color: var(--accent);
    margin-top: 6px;
    line-height: 1;
  }
  .rule {
    position: absolute;
    left: 18px;
    right: 24px;
    border-top: 1px dashed var(--accent);
  }
  .rule--top { top: 111px; }
  .rule--bottom { top: 225px; }

  .contact {
    position: absolute;
    left: 22px;
    top: 127px;
    list-style: none;
  }
  .contact__item {
    display: flex;
    align-items: center;
    height: 29px;
    font-weight: 300;
    font-size: 15px;
    letter-spacing: 0.1em;
  }
  .contact__icon {
    width: 17px;
    height: 15px;
    margin-right: 8px;
    flex: none;
  }
  .address {
    position: absolute;
    left: 0;
    right: 0;
    top: 243px;
    text-align: center;
    font-style: normal;
  }
  .address__pin { width: 14px; height: 17px; display: block; margin: 0 auto 5px; }
  .address__venue {
    font-weight: 400;
    font-size: 20px;
    letter-spacing: 0.08em;
    line-height: 1.1;
  }
  .address__line {
    font-weight: 400;
    font-size: 15px;
    letter-spacing: 0.09em;
    line-height: 18px;
  }
</style>
</head>
<body>

  <section class="card card--front" aria-label="Card front">
    <div class="brand">
      <span class="brand__dot" aria-hidden="true"></span>
      <span class="brand__name">GOLD TIDE PICTURES</span>
    </div>
  </section>

  <section class="card card--back" aria-label="Card back">
    <div class="back__panel">
      <div class="brand">
        <span class="brand__dot" aria-hidden="true"></span>
        <span class="brand__name">GOLD TIDE PICTURES</span>
      </div>
    </div>

    <div class="details">
      <header class="person">
        <h1 class="person__name">Neil Parker</h1>
        <p class="person__title">Managing Partner</p>
      </header>

      <div class="rule rule--top"></div>

      <ul class="contact">
        <li class="contact__item">
          <svg class="contact__icon" viewBox="0 0 24 24" aria-hidden="true">
            <path fill="var(--accent)" d="M6.6 10.8a15.5 15.5 0 0 0 6.6 6.6l2.2-2.2c.3-.3.7-.4 1-.2 1.1.4 2.3.6 3.6.6.6 0 1 .4 1 1V20c0 .6-.4 1-1 1A17 17 0 0 1 3 4c0-.6.4-1 1-1h3.5c.6 0 1 .4 1 1 0 1.3.2 2.5.6 3.6.1.3 0 .7-.2 1z"/>
          </svg>
          <span>(310) 555 0148</span>
        </li>
        <li class="contact__item">
          <svg class="contact__icon" viewBox="0 0 24 18" aria-hidden="true">
            <rect x="1" y="1" width="22" height="16" fill="none" stroke="var(--accent)" stroke-width="2"/>
            <path d="M1 1l11 9 11-9M1 17l8-7M23 17l-8-7" fill="none" stroke="var(--accent)" stroke-width="2"/>
          </svg>
          <span>neil@goldtidepicturesgroup.example</span>
        </li>
        <li class="contact__item">
          <svg class="contact__icon" viewBox="0 0 24 24" aria-hidden="true">
            <circle cx="10" cy="10" r="7" fill="none" stroke="var(--accent)" stroke-width="2.6"/>
            <path d="M15 15l7 7" stroke="var(--accent)" stroke-width="3" stroke-linecap="round"/>
          </svg>
          <span>goldtidepicturesgroup.example</span>
        </li>
      </ul>

      <div class="rule rule--bottom"></div>

      <address class="address">
        <svg class="address__pin" viewBox="0 0 14 18" aria-hidden="true">
          <path fill="var(--accent)" d="M7 0a7 7 0 0 0-7 7c0 5 7 11 7 11s7-6 7-11a7 7 0 0 0-7-7zm0 9.5A2.5 2.5 0 1 1 7 4.5a2.5 2.5 0 0 1 0 5z"/>
        </svg>
        <div class="address__venue">KTW Studio Park</div>
        <div class="address__line">2250 Halverd Street</div>
        <div class="address__line">Harbor Wing, 4th Floor</div>
        <div class="address__line">Manhattan Beach, CA 90412</div>
      </address>
    </div>
  </section>

</body>
</html>
```